R7M Horizon Business Card Design

We need a business card created for our New Business "R7M Horizon"<br/><br/>The business card design is up to you however the following information must be on the business card:<br/><br/>Front of the business card -<br/>Email :darrenp@r7mhorizon.nz<br/>Mobile: +64 (0) 22 4870 619<br/>Website: www.r7mhorizon.nz<br/>Card Owner Name: Darren Paltrow<br/>Company Title: Business Development Manager<br/>Slogan: "The BEST of both worlds". <br/>Logo On the front attached to the design brief<br/><br/>On the back: <br/>Space on the back for 4 more versions of the logo across the bottom of the card indicating different subsidiary brands - R7M Coffee, R7M Arts, R7M ?? (The card will be used for all of these brands - We Will add the extra subsidiary logos to the design once the design is finished (We are a graphics design team). <br/><br/>Other than that we want a premium feeling logo that remains universally usable depending on the business entity that we are using the card for. The use of bright bold colours would be great but we still want the card to feel premium.
Target Market(s)
Gift Design and Manufacturing Companies
Contact Information for Business Card
Front of the business card -
Email :darrenp@r7mhorizon.nz
Mobile: +64 (0) 22 4870 619
Website: www.r7mhorizon.nz
Card Owner Name: Darren Paltrow
Company Title: Business Development Manager
Slogan: "The BEST of both worlds".
Logo On the front attached to the design brief

```html
<!DOCTYPE html>
<html lang="en">
<head>
<meta charset="utf-8">
<title>R7M Horizon — Business Card</title>
<link rel="stylesheet" href="https://fonts.googleapis.com/css2?family=Exo+2:ital,wght@0,400;0,600;0,700;0,800;1,400&display=swap">
<style>
  :root {
    --brand-blue: #3444a0;
    --brand-blue-light: #3d4fb0;
    --paper: #ffffff;
    --arc-dark: #3a3a3c;
    --backdrop: #2a2a2c;
    --card-w: 700px;
    --card-h: 400px;
  }
  * { box-sizing: border-box; margin: 0; padding: 0; }
  html, body {
    width: 1200px;
    height: 900px;
    overflow: hidden;
    background: var(--backdrop);
    font-family: "Exo 2", sans-serif;
  }
  .sheet {
    position: relative;
    width: 1200px;
    height: 900px;
  }
  .card {
    position: absolute;
    left: 250px;
    width: var(--card-w);
    height: var(--card-h);
    border-radius: 22px;
    overflow: hidden;
    background: linear-gradient(135deg, var(--brand-blue) 0%, var(--brand-blue-light) 100%);
    color: var(--paper);
  }
  .card--back { top: 35px; }
  .card--front { top: 465px; }

  /* Wordmark stand-in */
  .wordmark {
    position: absolute;
    display: flex;
    align-items: center;
    gap: 14px;
    font-weight: 700;
    letter-spacing: 0.5px;
    white-space: nowrap;
  }
  .wordmark__dot {
    border-radius: 50%;
    flex: none;
  }
  .card--back .wordmark {
    left: 50%;
    top: 150px;
    transform: translateX(-50%);
    font-size: 62px;
    color: var(--paper);
  }
  .card--back .wordmark__dot {
    width: 26px; height: 26px;
    background: var(--paper);
  }

  /* Slogan */
  .slogan {
    position: absolute;
    display: flex;
    align-items: center;
    gap: 8px;
    font-size: 19px;
    font-weight: 400;
    white-space: nowrap;
  }
  .slogan strong { font-weight: 800; }
  .slogan__arrow { width: 12px; height: 10px; fill: var(--paper); }
  .card--back .slogan {
    left: 50%;
    bottom: 38px;
    transform: translateX(-50%);
  }
  .card--front .slogan {
    left: 40px;
    bottom: 34px;
    font-size: 22px;
  }

  /* Front side */
  .front-art {
    position: absolute;
    inset: 0;
  }
  .card--front .wordmark {
    left: 430px;
    top: 190px;
    font-size: 40px;
    color: var(--brand-blue);
    gap: 10px;
  }
  .card--front .wordmark__dot {
    width: 18px; height: 18px;
    background: var(--brand-blue);
  }
  .holder {
    position: absolute;
    left: 40px;
    top: 74px;
  }
  .holder__name {
    font-size: 30px;
    font-weight: 800;
    letter-spacing: 2.5px;
    text-transform: uppercase;
    line-height: 1;
  }
  .holder__title {
    font-size: 18px;
    font-weight: 400;
    letter-spacing: 0.4px;
    margin-top: 8px;
  }
  .contacts {
    list-style: none;
    position: absolute;
    left: 40px;
    top: 162px;
    font-size: 18px;
    line-height: 30px;
  }
  .contacts li {
    display: flex;
    align-items: center;
    gap: 12px;
  }
  .contacts svg {
    width: 15px; height: 15px;
    fill: none;
    stroke: var(--paper);
    stroke-width: 1.6;
    flex: none;
  }
</style>
</head>
<body>
<main class="sheet">

  <section class="card card--back" aria-label="Card back">
    <div class="wordmark">
      <span>R7M Horizon</span>
      <span class="wordmark__dot"></span>
    </div>
    <p class="slogan">
      <svg class="slogan__arrow" viewBox="0 0 12 10"><polygon points="12,0 12,10 0,5"/></svg>
      <span>The <strong>BEST</strong> of both worlds</span>
      <svg class="slogan__arrow" viewBox="0 0 12 10"><polygon points="0,0 0,10 12,5"/></svg>
    </p>
  </section>

  <section class="card card--front" aria-label="Card front">
    <svg class="front-art" viewBox="0 0 700 400" aria-hidden="true">
      <circle cx="628" cy="206" r="246" fill="var(--arc-dark)"/>
      <circle cx="640" cy="210" r="240" fill="var(--paper)"/>
    </svg>

    <div class="holder">
      <h1 class="holder__name">Darren Paltrow</h1>
      <p class="holder__title">Business Development Manager</p>
    </div>

    <ul class="contacts">
      <li>
        <svg viewBox="0 0 16 16"><path d="M4 1.5 L6 4.5 L4.6 6 C5.4 8 7.8 10.6 10 11.4 L11.5 10 L14.5 12 L13 14.5 C7.5 14 2 8.5 1.5 3 Z"/></svg>
        <span>+64 (0) 22 4870 619</span>
      </li>
      <li>
        <svg viewBox="0 0 16 16"><rect x="1.5" y="3.5" width="13" height="9" rx="1"/><polyline points="1.5,4 8,9 14.5,4"/></svg>
        <span>darrenp@r7mhorizon.nz</span>
      </li>
      <li>
        <svg viewBox="0 0 16 16"><circle cx="8" cy="8" r="6.5"/><ellipse cx="8" cy="8" rx="2.8" ry="6.5"/><line x1="1.5" y1="8" x2="14.5" y2="8"/></svg>
        <span>www.r7mhorizon.nz</span>
      </li>
    </ul>

    <div class="wordmark">
      <span>R7M Horizon</span>
      <span class="wordmark__dot"></span>
    </div>

    <p class="slogan">
      <svg class="slogan__arrow" viewBox="0 0 12 10"><polygon points="12,0 12,10 0,5"/></svg>
      <span>The <strong>BEST</strong> of both worlds</span>
      <svg class="slogan__arrow" viewBox="0 0 12 10"><polygon points="0,0 0,10 12,5"/></svg>
    </p>
  </section>

</main>
</body>
</html>
```